Ashmoor Web Design Project

I need the front page and an internal page designed for this client's website. The logo is attached. Obviously the colors have to go with and/or work with the logo colors. I also attached a very rough brochure layout to help you see the direction we're going in with print materials. The rough site map is also attached. I see a slider on the homepage, the art for which I may come back to you to create. This clinic is in a very high end Dallas neighborhood. The hook is that it's a primary care and urgent facility with convenient hours.

I don't know how much this impacts your design, but this will be a Wordpress site and I'm using a framework called Brovila (brovila.com). If Brovila proves to be inflexible, I'll have to get a template that allows me to execute your design.

This site (http://lanternvaleclinic.com) has the type and quality of content I will eventually have on the Ashmoor site.

I just revised the brief for this project. I added the site map and added details to the overview and the "Must Have" section. Thank you for revisiting the brief. 

Reason: Christmas was a bad time to end it.

Target Market(s)

Women 25-54 with children living at home, income over $150k/year

Industry/Entity Type

Clinic

Requirements
Must have
• Masthead incorporating the logo
Followed by the primary nav
Slider on the home page below that
Dual nav - 1 with the nav in the attached site map
2 secondary nav with areas of healthcare
There will three blocks under the nav
1. It's about time (with a small blurb less than 50 words.
2. It's about choices (with small blurb)
3. It's about you (with small blurb)
Three footer blocks
patient check in link on every page
"No appointment? No problem" icon on every page

```html
<!DOCTYPE html>
<html lang="en">
<head>
<meta charset="utf-8">
<title>Ashmoor Medical – Home</title>
<link rel="stylesheet" href="https://fonts.googleapis.com/css2?family=Open+Sans:wght@400;600;700&family=Delius&family=Arimo:wght@400;700&display=swap">
<style>
  :root{
    --blue:#0b64a8;
    --blue-dark:#0a4f8f;
    --blue-bright:#1a8fe3;
    --green:#22b35e;
    --green-soft:#3dbd6e;
    --text:#333;
    --muted:#555;
    --white:#fff;
  }
  *{margin:0;padding:0;box-sizing:border-box}
  html,body{width:1200px;height:1200px;overflow:hidden;background:var(--white)}
  body{position:relative;font-family:"Arimo",Arial,sans-serif;color:var(--text)}
  .abs{position:absolute}

  /* masthead */
  .brand-name{left:130px;top:32px;font-family:"Open Sans",sans-serif;font-weight:600;font-size:22px;color:var(--blue)}
  .brand-tag{left:131px;top:64px;font-family:"Open Sans",sans-serif;font-size:10px;color:var(--muted)}
  .util-links{right:130px;top:18px;font-family:"Open Sans",sans-serif;font-size:11px;color:var(--muted);display:flex;gap:9px}
  .util-links span::before{content:"> "}

  /* primary nav */
  .main-nav{left:0;top:100px;width:1200px;height:34px;background:var(--blue)}
  .main-nav ul{list-style:none;display:flex;margin-left:130px;height:34px}
  .main-nav li{font-family:"Open Sans",sans-serif;font-size:10.5px;font-weight:700;color:var(--white);padding:0 13.5px;line-height:34px}
  .main-nav li.active{background:var(--green);padding:0 10px}

  /* slider */
  .hero-band{left:0;top:134px;width:1200px;height:240px;background:linear-gradient(#ececec,#fafafa 70%,#e8e8e8)}
  .hero-photo{left:130px;top:134px;width:581px;height:240px;background:linear-gradient(100deg,#d8d8d6 0%,#bfc3c6 35%,#c9b8a8 60%,#dcd6cc 100%)}
  .hero-panel{left:711px;top:134px;width:359px;height:240px;background:var(--green);overflow:hidden;color:var(--white);font-family:"Open Sans",sans-serif}
  .hero-panel svg{position:absolute;right:0;bottom:0}
  .hero-title{position:absolute;left:29px;top:17px;font-size:16px;font-weight:600;text-transform:uppercase}
  .hero-text{position:absolute;left:29px;top:47px;width:300px;font-size:12.2px;line-height:16.8px}
  .hero-btn{position:absolute;left:30px;top:166px;width:102px;height:30px;border:2px solid var(--white);border-radius:16px;display:flex;align-items:center;font-size:12px;font-weight:700}
  .hero-btn .dot{width:18px;height:18px;border-radius:50%;background:var(--white);margin:0 10px 0 4px;display:flex;align-items:center;justify-content:center}

  /* sidebar */
  .care-box{left:130px;top:409px;width:220px;height:321px;background:linear-gradient(var(--blue-bright),var(--blue-dark));overflow:hidden;box-shadow:0 0 2px rgba(0,0,0,.3)}
  .care-photo{position:absolute;left:0;top:0;width:220px;height:94px;background:linear-gradient(90deg,#b78d6c,#d9c2a8 50%,#9aaab6)}
  .care-box svg{position:absolute;left:0;top:60px}
  .care-title{position:absolute;left:31px;top:115px;font-family:"Open Sans",sans-serif;font-weight:700;font-size:12px;color:var(--white)}
  .care-list{position:absolute;left:31px;top:140px;list-style:none;font-family:"Open Sans",sans-serif;font-size:12.3px;color:var(--white)}
  .care-list li{height:24px;line-height:18px}
  .care-list li::before{content:"»";font-weight:700;margin-right:8px;font-size:14px}

  .side-link{left:132px;display:flex;align-items:center;font-weight:700;font-size:12px;color:var(--blue)}
  .side-link .ico{width:24px;height:24px;border-radius:50%;background:var(--blue);margin-right:11px;display:flex;align-items:center;justify-content:center}
  .side-text{left:130px;top:788px;width:220px;font-size:12px;line-height:14.3px}
  .dotted{left:130px;top:850px;width:220px;border-top:1px dotted var(--blue)}

  /* content */
  .section-h{font-weight:700;font-size:14px;color:var(--blue)}
  .about{left:370px;top:437px;width:378px;font-size:12px;line-height:14.4px}
  .about p{text-indent:36px;margin-bottom:9px}
  .video{left:769px;top:441px;width:300px;height:165px;background:linear-gradient(90deg,#aeb6bd,#dfe3e6 50%,#b9c3cb);overflow:hidden}
  .video-title{position:absolute;left:34px;top:7px;font-size:9px;color:#3aa7f0;background:rgba(0,0,0,.55);padding:1px 4px}
  .video-sub{position:absolute;left:34px;top:22px;font-size:7px;color:#fff}
  .video-side{position:absolute;right:6px;width:24px;height:18px;background:rgba(0,0,0,.75);border-radius:2px}
  .video-bar{position:absolute;left:4px;bottom:4px;width:292px;height:20px;display:flex;gap:3px}
  .video-play{width:36px;background:rgba(0,0,0,.8);border-radius:2px;display:flex;align-items:center;justify-content:center}
  .video-track{flex:1;background:rgba(0,0,0,.8);border-radius:2px;position:relative}
  .video-track::after{content:"";position:absolute;left:6px;top:8px;width:54px;height:4px;background:#3aa7f0}

  .pillar{top:639px;width:220px}
  .pillar h3{font-family:"Delius",cursive;font-weight:400;font-size:16px;color:var(--blue);padding-bottom:5px;border-bottom:2px solid var(--green-soft);-webkit-text-stroke:.3px var(--blue)}
  .pillar p{font-size:12px;line-height:14.3px;margin-top:16px}
  .pillar p+p{margin-top:8px}

  /* footer */
  .footer{left:130px;top:940px;width:940px;height:150px;background:var(--green-soft);color:var(--white);font-family:"Open Sans",sans-serif}
  .footer-col{position:absolute;top:0;height:150px;padding-top:17px}
  .footer-col h4{font-size:12px;font-weight:700;text-transform:uppercase;margin-bottom:13px}
  .footer-col p{font-size:11px;line-height:15.7px}
  .footer-col a{color:var(--white)}
  .divider{position:absolute;top:10px;height:138px;border-left:1px dotted var(--white)}
  .social{display:flex;align-items:center;margin-bottom:4px;font-size:11px}
  .social .sq{width:26px;height:26px;background:#2f8fd8;border-radius:3px;margin-right:19px}
  .footer-bar{left:130px;top:1090px;width:940px;height:50px;background:var(--green);color:var(--white);font-family:"Open Sans",sans-serif;font-size:11px;text-align:center;line-height:50px}
</style>
</head>
<body>

<header>
  <div class="abs brand-name">Ashmoor Medical</div>
  <div class="abs brand-tag">Immediate Family and Personal Care</div>
  <nav class="abs util-links"><span>Register</span><span>Login</span><span>Blog</span></nav>
</header>

<nav class="abs main-nav">
  <ul>
    <li class="active">HOME</li><li>ABOUT</li><li>SERVICES</li><li>STAFF</li><li>INSURANCE</li><li>VIDEOS</li><li>CONTACT US</li>
  </ul>
</nav>

<section class="hero">
  <div class="abs hero-band"></div>
  <div class="abs hero-photo" role="img" aria-label="Photo of a smiling senior doctor with his medical team"></div>
  <div class="abs hero-panel">
    <svg width="200" height="200" viewBox="0 0 200 200" aria-hidden="true">
      <circle cx="200" cy="200" r="60" fill="none" stroke="rgba(255,255,255,.07)" stroke-width="18"/>
      <circle cx="200" cy="200" r="110" fill="none" stroke="rgba(255,255,255,.06)" stroke-width="18"/>
      <circle cx="200" cy="200" r="160" fill="none" stroke="rgba(255,255,255,.05)" stroke-width="18"/>
    </svg>
    <h2 class="hero-title">Title of slide one</h2>
    <p class="hero-text">Lorem ipsum dolor sit amet, consectetur adipiscing elit. Praesent porttitor leo at lorem ultrices ac adipiscing mauris fringilla. Nunc vestibulum fermentum augue, ac blandit massa molestie quis. Aenean vestibulum sapien eget sapien viverra mollis.</p>
    <div class="hero-btn"><span class="dot"><svg width="10" height="10" viewBox="0 0 10 10"><path d="M1 5h7M5 2l3 3-3 3" stroke="#22b35e" stroke-width="1.8" fill="none"/></svg></span>Button</div>
  </div>
</section>

<aside>
  <div class="abs care-box">
    <div class="care-photo" role="img" aria-label="Photo of a happy family of three"></div>
    <svg width="220" height="50" viewBox="0 0 220 50" aria-hidden="true"><path d="M0 10 Q110 50 220 30 V50 H0 Z" fill="#1a8fe3"/></svg>
    <h3 class="care-title">AREAS OF HEALTHCARE</h3>
    <ul class="care-list">
      <li>Immediate Care</li><li>Allergies</li><li>Primary Care</li><li>Women’s Health</li><li>Medical Spa Treatments</li><li>Men’s Health</li><li>Weight Loss</li>
    </ul>
  </div>
  <div class="abs side-link" style="top:750px"><span class="ico"><svg width="12" height="12" viewBox="0 0 12 12"><rect x="2" y="1.5" width="8" height="9.5" fill="none" stroke="#fff" stroke-width="1.3"/><path d="M4 5h4M4 7.5h4" stroke="#fff" stroke-width="1.2"/></svg></span>Patient Check In</div>
  <p class="abs side-text">Lorem ipsum dolor sit amet, consectetur adipiscing elit. Sed ut risus a massa varius viverra.</p>
  <div class="abs dotted"></div>
  <div class="abs side-link" style="top:861px"><span class="ico"><svg width="12" height="12" viewBox="0 0 12 12"><rect x="1" y="3" width="10" height="7" rx="1" fill="#fff"/><rect x="4" y="1.5" width="4" height="2" fill="none" stroke="#fff"/></svg></span>No Appointment, No Proglem</div>
</aside>

<main>
  <h2 class="abs section-h" style="left:370px;top:406px">About Ashmoor Medical</h2>
  <div class="abs about">
    <p>Lorem ipsum dolor sit amet, consectetur adipiscing elit. In ut est ac lacus ultrices eleifend. Quisque malesuada est tristique augue luctus eleifend.</p>
    <p>Pellentesque a quam ac lectus pulvinar imperdiet. Nulla facilisi. Suspendisse commodo elit ut justo malesuada sit amet suscipit quam eleifend. Integer at dui sem, eu iaculis risus. Nulla suscipit massa vel lacus hendrerit vel congue lectus vulputate. Duis dictum mi quis lectus lacinia eget consequat sem pretium. Pellentesque eu enim enim, eget tempor tortor.</p>
  </div>

  <h2 class="abs section-h" style="left:769px;top:408px">Interactive Content</h2>
  <div class="abs video" role="img" aria-label="Video still of two nurses reviewing a chest x-ray">
    <span class="video-title">Clinic tour video</span>
    <span class="video-sub">from clinic</span>
    <span class="video-side" style="top:5px"></span>
    <span class="video-side" style="top:27px"></span>
    <span class="video-side" style="top:49px"></span>
    <div class="video-bar">
      <span class="video-play"><svg width="10" height="10" viewBox="0 0 10 10"><path d="M2 1l7 4-7 4z" fill="#fff"/></svg></span>
      <span class="video-track"></span>
    </div>
  </div>

  <article class="abs pillar" style="left:370px">
    <h3>It’s about time</h3>
    <p>Lorem ipsum dolor sit amet, consectetur adipiscing elit. Sed ut risus a massa varius viverra. In hac habitasse platea dictumst. Quisque faucibus pulvinar mi et luctus.</p>
    <p>Duis lacus augue, malesuada sed dignissim ut, tincidunt quis ante. Nunc ultrices odio ac elit tempor.</p>
  </article>
  <article class="abs pillar" style="left:610px">
    <h3>It’s about choices</h3>
    <p>Lorem ipsum dolor sit amet, consectetur adipiscing elit. Sed ut risus a massa varius viverra. In hac habitasse platea dictumst. Quisque faucibus pulvinar mi et luctus.</p>
    <p>Duis lacus augue, malesuada sed dignissim ut, tincidunt quis ante. Nunc ultrices odio ac elit tempor.</p>
  </article>
  <article class="abs pillar" style="left:850px">
    <h3>It’s about you</h3>
    <p>Lorem ipsum dolor sit amet, consectetur adipiscing elit. Sed ut risus a massa varius viverra. In hac habitasse platea dictumst. Quisque faucibus pulvinar mi et luctus.</p>
    <p>Duis lacus augue, malesuada sed dignissim ut, tincidunt quis ante. Nunc ultrices odio ac elit tempor.</p>
  </article>
</main>

<footer>
  <div class="abs footer">
    <div class="footer-col" style="left:40px;width:250px">
      <h4>Here goes transparent logo</h4>
      <p>Copyright ©2012 Ashmoor Medical<br>All rights reserved.<br>Ashmoor collects information you provide on this website. To learn more, please read the <a href="#">Privacy Policy</a>.</p>
    </div>
    <span class="divider" style="left:310px"></span>
    <div class="footer-col" style="left:349px;width:240px">
      <h4>Contact with Ashmoor Medical</h4>
      <p style="font-weight:700;margin-bottom:10px">(214) 555 0142</p>
      <p style="font-weight:700;margin-bottom:10px">AshmoorFamilyMedical.com</p>
      <p>4270 Ashmoor Ave (at Elm Pkwy) Ste 210,<br>Dallas, TX 75230</p>
    </div>
    <span class="divider" style="left:600px"></span>
    <div class="footer-col" style="left:639px;width:260px">
      <h4>Connect with Ashmoor Medical</h4>
      <div class="social"><span class="sq"></span><a href="#">Like us on Chatterly</a></div>
      <div class="social"><span class="sq"></span><a href="#">Follow us @ashmoormedical</a></div>
      <p style="margin-left:45px;font-size:11px"><a href="#">on Tweetly</a></p>
    </div>
  </div>
  <nav class="abs footer-bar">About Us| New Patients | Insurance &amp; Billing | Our Medical Clinic | Our Staff | FAQ | Sitemap | Contact Us | Privacy Policy</nav>
</footer>

</body>
</html>
```